Business card for a new innovative and professional lawn care business

We need a business card design for a new lawn care business in Halifax NS Canada. We offer lawn services in Halifax & Bedford. Our services offered include lawn care, garden services, and property maintenance. We take pride in our work and are experienced at what we do. I would like to see a design that is double sided. On the backside I would like the something simple (maybe my logo preferably on blackround (linked below) with website link, Facebook page or something). The front I want to include contact info:
Morgan Pell
phone 902-555-0148
email - brookvaleyards.ca
facebook - friendpage.com/brookvaleyards
Instagram maybe ? - snapgrid.com/brookvaleyard
Serving Halifax and Bedford for 5 years?
I don't want it to have too much information as I will be passing them out in aim to visit website, or call !
We do want it to include lawn care, garden services and property maintenance.
Basic, catchy, and modern looking !
Logo attached below !

Target Market(s)

Passing business cards to everyone I meet or interact with.

Industry/Entity Type

Lawn Care

Contact Information for Business Card

Double sided with some basic information, with catchy colours and easy to look at.

Font styles to use
Sans Serif

Requirements
Must have
• Must be double sided and have :
• Name, Phone, Email, FB, Website, and 3 main services offered - lawn care, property maintenance, garden services
Nice to have
• Would be nice to have instagram link if it goes well on there
Should not have
• Don't want too much writing or images that are distracting

```html
<!DOCTYPE html>
<html lang="en">
<head>
<meta charset="utf-8">
<title>Brookvale Yards – Business Card</title>
<link href="https://fonts.googleapis.com/css2?family=Open+Sans:wght@400;600;700;800&display=swap" rel="stylesheet">
<style>
  :root {
    --forest: #157235;
    --lime: #8cc63f;
    --white: #ffffff;
    --ink: #1e5e30;
    --backdrop: #2e2f30;
  }
  * { margin: 0; padding: 0; box-sizing: border-box; }
  html, body {
    width: 1200px; height: 900px; overflow: hidden;
    background: var(--backdrop);
    font-family: "Open Sans", Arial, sans-serif;
  }
  .card {
    position: absolute; left: 250px;
    width: 700px; height: 400px;
    border-radius: 28px; overflow: hidden;
    background: var(--white);
  }
  .card--back { top: 36px; }
  .card--front { top: 464px; }

  .brand {
    position: absolute; display: flex; align-items: center; gap: 14px;
    color: var(--forest); font-weight: 800; letter-spacing: 1px;
    white-space: nowrap;
  }
  .brand__dot { width: 22px; height: 22px; border-radius: 50%; background: var(--lime); flex: none; }
  .card--back .brand { left: 0; right: 0; justify-content: center; top: 150px; font-size: 44px; }
  .card--front .brand { left: 48px; top: 92px; font-size: 38px; }

  .socials {
    position: absolute; left: 36px; right: 36px; bottom: 38px;
    display: flex; justify-content: space-between;
    color: var(--ink); font-size: 18px; font-weight: 600;
    white-space: nowrap;
  }
  .socials__item { display: flex; align-items: center; gap: 10px; }
  .socials__mark { width: 16px; height: 16px; border-radius: 3px; background: var(--forest); flex: none; }

  .swoosh { position: absolute; inset: 0; }

  .services {
    position: absolute; right: 345px; top: 268px;
    text-align: right; color: var(--white); font-size: 19px; line-height: 27px;
    white-space: nowrap;
  }
  .services__title { color: var(--lime); font-weight: 700; font-size: 21px; letter-spacing: .5px; }
  .services__item::after {
    content: ""; display: inline-block; width: 8px; height: 8px; border-radius: 50%;
    background: var(--lime); margin-left: 9px; vertical-align: middle;
  }

  .contact { position: absolute; left: 392px; top: 222px; color: var(--white); white-space: nowrap; }
  .contact__name { color: var(--lime); font-weight: 700; font-size: 30px; line-height: 36px; margin-bottom: 6px; }
  .contact__line { display: flex; align-items: center; gap: 10px; font-size: 18px; line-height: 29px; }
  .contact__icon { width: 15px; height: 15px; flex: none; }
</style>
</head>
<body>

<section class="card card--back" aria-label="Card back">
  <div class="brand"><span class="brand__dot"></span>BROOKVALE YARDS</div>
  <div class="socials">
    <div class="socials__item"><span class="socials__mark"></span>friendpage.com/brookvaleyards</div>
    <div class="socials__item"><span class="socials__mark"></span>snapgrid.com/brookvaleyard</div>
  </div>
</section>

<section class="card card--front" aria-label="Card front">
  <svg class="swoosh" width="700" height="400" viewBox="0 0 700 400">
    <path d="M0,262 C220,250 500,170 700,52 L700,400 L0,400 Z" fill="var(--lime)"/>
    <path d="M0,270 C220,258 505,180 700,64 L700,400 L0,400 Z" fill="var(--forest)"/>
  </svg>

  <div class="brand"><span class="brand__dot"></span>BROOKVALE YARDS</div>

  <div class="services">
    <div class="services__title">SERVICES</div>
    <div class="services__item">Lawn care</div>
    <div class="services__item">Garden services</div>
    <div class="services__item">Property maintenance</div>
  </div>

  <div class="contact">
    <div class="contact__name">MORGAN PELL</div>
    <div class="contact__line">
      <svg class="contact__icon" viewBox="0 0 16 16"><path d="M4 1 L6.5 4.5 L5 6.5 C6 8.5 7.5 10 9.5 11 L11.5 9.5 L15 12 L13 15 C7 15 1 9 1 3 Z" fill="var(--lime)"/></svg>
      902-555-0148
    </div>
    <div class="contact__line">
      <svg class="contact__icon" viewBox="0 0 16 16"><rect x="1" y="3" width="14" height="10" rx="1.5" fill="none" stroke="var(--lime)" stroke-width="1.6"/><path d="M1.5 4 L8 9 L14.5 4" fill="none" stroke="var(--lime)" stroke-width="1.6"/></svg>
      info@brookvaleyards.ca
    </div>
    <div class="contact__line">
      <svg class="contact__icon" viewBox="0 0 16 16"><circle cx="8" cy="8" r="6.5" fill="none" stroke="var(--lime)" stroke-width="1.5"/><ellipse cx="8" cy="8" rx="3" ry="6.5" fill="none" stroke="var(--lime)" stroke-width="1.2"/><path d="M1.5 8 H14.5" stroke="var(--lime)" stroke-width="1.2"/></svg>
      www.brookvaleyards.ca
    </div>
  </div>
</section>

</body>
</html>
```